Risk Management Company in need of Business Card Design

We sell risk management insurance to Lenders (Banks, Credit Unions, Real Estate Trust).

We need a very clean, professional card that will leave a great impression.

We are looking to use a blue color for our logo on the card (Preferably close to royal blue but are open to looking at navy blue or any darker blues as well).

Please see the logo attached to get an idea. We are open to writing Harbor Ledger Under the logo or next to the logo. Really whatever looks best.

Target Market(s)

Banks, Credit Unions, Real Estate Trusts

Industry/Entity Type

Insurance

Contact Information for Business Card

Name: Tom Brandish
Title: Regional Sales Director
Email: tbrandish@harborledger-example.net
C:410-555-0137
D:410-555-0182
888-555-0149 Ext.418
F:443-555-0164 (We would like to see some cards without the fax number as well to compare)

Company Name: Harbor Ledger
Website: www.harborledger-example.net

Address: 718 E. Marlow St. Suite 340, Larkdale, PA 21287 (Preferably written on the bottom of the card in small print.)

Colors
0355a3
0455a3

Requirements
Nice to have
• We would like to see a couple of where the back has the logo in reverse colors (Logo White, Background Blue)

```html
<!DOCTYPE html>
<html lang="en">
<head>
<meta charset="utf-8">
<title>Harbor Ledger – Business Card</title>
<link rel="stylesheet" href="https://fonts.googleapis.com/css2?family=Source+Sans+3:wght@400;600&display=swap">
<style>
  :root {
    --backdrop: #e9e7e3;
    --card-white: #ffffff;
    --slate: #33505f;
    --royal: #1b4fae;
    --ink: #333b40;
    --rule: #c9cdd0;
    --on-dark: #ffffff;
  }
  * { margin: 0; padding: 0; box-sizing: border-box; }
  html, body { width: 1200px; height: 505px; overflow: hidden; }
  body {
    background: var(--backdrop);
    font-family: "Source Sans 3", "Myriad Pro", Arial, sans-serif;
    color: var(--ink);
    position: relative;
  }
  .card {
    position: absolute;
    top: 98px;
    width: 540px;
    height: 310px;
    overflow: hidden;
    box-shadow: 0 6px 18px rgba(0,0,0,.18);
  }
  .card--front { left: 40px; background: var(--card-white); }
  .card--back  { left: 620px; background: var(--slate); }

  /* front */
  .front-brand {
    position: absolute;
    left: 0; top: 0;
    width: 255px; height: 250px;
    display: flex; align-items: center; justify-content: center;
  }
  .wordmark {
    font-weight: 600;
    color: var(--slate);
    letter-spacing: .06em;
    text-transform: uppercase;
    white-space: nowrap;
  }
  .front-brand .wordmark { font-size: 25px; }
  .divider {
    position: absolute;
    left: 258px; top: 32px;
    width: 1px; height: 178px;
    background: var(--rule);
  }
  .contact {
    position: absolute;
    left: 276px; top: 28px;
    font-size: 13.5px;
    line-height: 1.2;
    white-space: nowrap;
  }
  .contact-address { margin-bottom: 12px; }
  .contact-list { list-style: none; }
  .contact-list li {
    display: flex; align-items: center;
    gap: 8px;
    margin-bottom: 6px;
  }
  .contact-list svg { width: 12px; height: 12px; flex: none; fill: var(--ink); }
  .ext { font-size: 9px; vertical-align: super; }

  .band { position: absolute; inset: 0; width: 540px; height: 310px; }
  .signature {
    position: absolute;
    right: 30px; top: 246px;
    text-align: center;
    color: var(--on-dark);
  }
  .signature-name { font-weight: 600; font-size: 18px; line-height: 1.1; }
  .signature-title { font-size: 16px; line-height: 1.25; }

  /* back */
  .back-brand {
    position: absolute;
    inset: 0;
    display: flex; flex-direction: column;
    align-items: center; justify-content: center;
    gap: 14px;
  }
  .back-brand .wordmark { font-size: 50px; color: var(--on-dark); }
  .back-url {
    font-weight: 600;
    font-size: 17px;
    letter-spacing: .12em;
    color: var(--on-dark);
  }
</style>
</head>
<body>

<section class="card card--front" aria-label="Business card front">
  <div class="front-brand">
    <span class="wordmark">Harbor Ledger</span>
  </div>

  <div class="divider"></div>

  <div class="contact">
    <p class="contact-address">718 E. Marlow St.<br>Suite 340, Larkdale<br>PA 21287</p>
    <ul class="contact-list">
      <li>
        <svg viewBox="0 0 12 12" aria-hidden="true"><path d="M2.5 1 4.5 3 3.6 4.4c.8 1.6 2.2 3 3.9 3.9L9 7.5l2 2-1.4 1.4C5.8 10.5 1.5 6.2 1.1 2.4Z"/></svg>
        <span>410-555-0182</span>
      </li>
      <li>
        <svg viewBox="0 0 12 12" aria-hidden="true"><path d="M2.5 1 4.5 3 3.6 4.4c.8 1.6 2.2 3 3.9 3.9L9 7.5l2 2-1.4 1.4C5.8 10.5 1.5 6.2 1.1 2.4Z"/></svg>
        <span>888-555-0149 <span class="ext">Ext.418</span></span>
      </li>
      <li>
        <svg viewBox="0 0 12 12" aria-hidden="true"><rect x="3" y="1" width="6" height="3"/><rect x="1" y="5" width="10" height="4" rx="1"/><rect x="3" y="8" width="6" height="3"/></svg>
        <span>443-555-0164</span>
      </li>
      <li>
        <svg viewBox="0 0 12 12" aria-hidden="true"><path d="M1 3h10v7H1Z"/><path d="M1 3 6 7 11 3" fill="none" stroke="#fff" stroke-width="1"/></svg>
        <span>tbrandish@harborledger-example.net</span>
      </li>
      <li>
        <svg viewBox="0 0 12 12" aria-hidden="true"><circle cx="6" cy="6" r="5"/><path d="M1 6h10M6 1c-2.5 3-2.5 7 0 10M6 1c2.5 3 2.5 7 0 10" fill="none" stroke="#fff" stroke-width=".8"/></svg>
        <span>www.harborledger-example.net</span>
      </li>
    </ul>
  </div>

  <svg class="band" viewBox="0 0 540 310" aria-hidden="true">
    <polygon points="0,270 268,270 256,286 0,286" fill="var(--royal)"/>
    <polygon points="0,290 253,290 247,298 0,298" fill="var(--slate)"/>
    <polygon points="262,310 300,238 540,238 540,310" fill="var(--slate)"/>
  </svg>

  <div class="signature">
    <p class="signature-name">Tom Brandish</p>
    <p class="signature-title">Regional Sales Director</p>
  </div>
</section>

<section class="card card--back" aria-label="Business card back">
  <div class="back-brand">
    <span class="wordmark">Harbor Ledger</span>
    <span class="back-url">www.harborledger-example.net</span>
  </div>
</section>

</body>
</html>
```